KORVEL Group Pty Ltd. Website and Domain

www.korvelgroup.com.au

require email addresses setup.

Info@korvelgroup.com.au
accounts@korvelgroup.com.au
peter.halloway@korvelgroup.com.au
grant.whitley@korvelgroup.com.au

Website should promote commercial and domestic electrical services, audio visual services and data and fibre installations.

similar to my mates site www.brisvane.com.au

Website needs to promote professionalism, electrical/electrician, audio visual and data/fibre cabling installations.

promote environmental friendly imaginary.

Coding

```html
<!DOCTYPE html>
<html lang="en">
<head>
<meta charset="utf-8">
<title>KORVEL Group – Electrical, Audio Visual & Data</title>
<link href="https://fonts.googleapis.com/css2?family=Baumans&family=Hind:wght@400;500&family=Poppins:wght@400;500;600&family=Roboto:wght@300;400;700&display=swap" rel="stylesheet">
<style>
:root{
  --blue:#2f9fd9;
  --green:#a6ce39;
  --navy:#0e1430;
  --ink:#2b2b2b;
  --muted:#5b6b86;
  --light:#f1f2f5;
  --white:#ffffff;
}
*{margin:0;padding:0;box-sizing:border-box}
html,body{width:1200px;height:3891px;overflow:hidden}
body{position:relative;background:var(--white);font-family:"Hind",sans-serif;color:var(--ink)}
.abs{position:absolute}
.brand{display:flex;align-items:center;gap:10px;font-family:"Poppins",sans-serif;font-weight:600;color:var(--blue);letter-spacing:1px}
.brand-dot{border-radius:50%;border:4px solid var(--green)}

/* header */
.site-header{left:0;top:0;width:1200px;height:91px;background:var(--white)}
.site-header .brand{position:absolute;left:121px;top:18px;font-size:34px}
.site-header .brand-dot{width:56px;height:56px}
.main-nav{position:absolute;top:30px;left:491px;display:flex;font-family:"Hind",sans-serif;font-size:21px}
.main-nav a{color:#111;text-decoration:none;padding:0 30px;border-left:1px solid #ddd;line-height:30px}
.main-nav a:first-child{border:0;padding-left:0;color:var(--blue);text-decoration:underline;text-underline-offset:5px}

/* hero */
.hero{left:0;top:91px;width:1200px;height:586px;background:radial-gradient(ellipse at 70% 40%,#6b5044 0%,#3f3a39 40%,#222529 100%)}
.hero-call{left:128px;top:26px;color:var(--white);font-size:15px;line-height:17px;display:flex;gap:14px;align-items:center}
.hero-call b{font-weight:500;font-size:17px}
.hero-social{right:101px;top:28px;display:flex;gap:10px}
.hero-social span{width:29px;height:29px;border:2px solid var(--white);border-radius:50%}
.hero-title{left:0;width:1200px;top:245px;text-align:center;font-family:"Baumans",sans-serif;font-weight:400;color:var(--white);font-size:52px;line-height:64px}
.hero-arrow{top:247px}
.hero-dots{left:515px;top:524px;display:flex;gap:7px}
.hero-dots i{width:11px;height:11px;border:1.5px solid var(--white);border-radius:50%}
.hero-dots i.on{background:var(--green);border-color:var(--green)}

/* section titles */
.sec-title{left:0;width:1200px;text-align:center;font-family:"Roboto",sans-serif;font-weight:300;font-size:40px;color:#333}
.sec-title b{font-weight:700}
.rule{width:58px;height:4px;background:linear-gradient(90deg,var(--green),var(--blue));border-radius:2px}

/* about */
.about{left:0;top:677px;width:1200px;height:632px;background:linear-gradient(180deg,#f3f3f6 0%,#eceef2 70%,#d9dde4 100%)}
.emblem{display:flex;align-items:center;justify-content:center;border-radius:50%;border:16px solid var(--green);font-family:"Poppins",sans-serif;font-weight:600;color:var(--blue)}
.about .emblem{left:130px;top:120px;width:310px;height:310px;font-size:40px}
.about h2{left:582px;top:128px;font-family:"Roboto",sans-serif;font-weight:300;font-size:40px;color:#333}
.about h2 b{font-weight:700}
.about .rule{left:584px;top:180px}
.about-copy{left:582px;top:205px;width:430px;font-size:14px;line-height:25px;color:var(--muted)}
.about-copy p{margin-bottom:12px}
.about-copy .lead{font-size:16.5px;line-height:27px;color:#1b1b1b}

/* why */
.why-title{top:1385px}
.why-rule{left:571px;top:1443px}
.why-card{top:1485px;width:350px;height:337px;text-align:center}
.why-card.raised{background:var(--white);box-shadow:0 4px 26px rgba(0,0,0,.12)}
.why-card svg{margin-top:50px}
.why-card h3{margin-top:14px;font-family:"Roboto",sans-serif;font-weight:400;font-size:18.5px;color:#222}
.why-card p{margin:10px auto 0;width:270px;font-size:14px;line-height:24px;color:var(--muted)}

/* services */
.services{left:0;top:1949px;width:1200px;height:726px;background:radial-gradient(ellipse at 30% 30%,#e4e6ea 0%,#ebecef 45%,#f2f2f4 100%)}
.services .sec-title{top:70px}
.services .rule{left:571px;top:132px}
.services .emblem{left:446px;top:204px;width:310px;height:310px;font-size:40px}
.svc{font-family:"Poppins",sans-serif}
.svc h3{font-weight:600;font-size:20px;line-height:23px;color:#111}
.svc p{margin-top:12px;font-size:14.5px;line-height:24px;color:#333;width:200px}
.svc-icon{width:86px;height:86px}
.btn{display:flex;align-items:center;justify-content:center;background:var(--blue);color:var(--white);font-family:"Poppins",sans-serif;font-size:16px;border-radius:3px;text-decoration:none}
.services .btn{left:521px;top:568px;width:165px;height:46px}

/* testimonials */
.testi-title{top:2755px}
.testi-rule{left:571px;top:2811px}
.testi-card{top:2847px;width:275px;height:263px;background:var(--white);border:1px solid #ddd;padding:26px 32px;font-family:"Poppins",sans-serif}
.stars{color:#f7941d;font-size:17px;letter-spacing:2px}
.testi-card q{display:block;margin-top:8px;font-size:12.5px;font-weight:500;color:#222;quotes:"\201C" "\201D"}
.testi-card p{margin-top:12px;font-size:11px;line-height:20px;color:#666}
.author{display:flex;align-items:center;gap:10px;margin-top:28px;font-size:11px;line-height:15px;color:#444}
.author b{font-weight:600;color:#222}
.avatar{width:32px;height:32px;border-radius:50%;background:#8a8f96}
.testi-dots{left:564px;top:3150px;display:flex;gap:7px}
.testi-dots i{width:10px;height:10px;border:1.5px solid #8a9ab0;border-radius:50%}
.testi-dots i.on{background:var(--blue);border-color:var(--blue)}

/* contact band */
.cta{left:0;top:3256px;width:1200px;height:197px;background:var(--green);overflow:hidden}
.cta-text{left:446px;top:62px;font-family:"Poppins",sans-serif;font-size:28px;line-height:37px;color:var(--white);letter-spacing:.5px}
.cta-text b{font-weight:600}
.cta .btn{left:884px;top:79px;width:168px;height:41px;border-radius:21px;font-size:15px}

/* footer */
.site-footer{left:0;top:3483px;width:1200px;height:408px;background:var(--navy);color:#c9cfdc}
.site-footer .brand{position:absolute;left:166px;top:100px;font-size:36px}
.site-footer .brand-dot{width:56px;height:56px}
.foot-social{left:232px;top:215px;display:flex;gap:30px}
.foot-social span{width:16px;height:16px;border-radius:50%;background:var(--blue)}
.foot-links{left:509px;top:93px;list-style:none;font-size:16px;line-height:29px}
.foot-form input,.foot-form textarea{position:absolute;background:#eef2f9;border:1px solid #c7d0e0;border-radius:2px;font-family:"Hind",sans-serif;font-size:14px;padding:6px 11px;color:#7a879c}
.foot-form .btn{position:absolute;left:671px;top:278px;width:104px;height:35px;border:0;font-size:15px}
.foot-line{left:0;top:343px;width:1200px;height:1px;background:#262d4a}
.copyright{left:121px;top:363px;font-size:14px}
.legal{right:138px;top:363px;font-size:14px}
</style>
</head>
<body>

<header class="abs site-header">
  <div class="brand"><span class="brand-dot"></span>KORVEL</div>
  <nav class="main-nav">
    <a href="#">Home</a><a href="#">About us</a><a href="#">Services</a><a href="#">Gallery</a><a href="#">Contact</a>
  </nav>
</header>

<section class="abs hero" role="img" aria-label="Electrician working on a cabling panel">
  <div class="abs hero-call">
    <svg width="36" height="36" viewBox="0 0 24 24" fill="none" stroke="#fff" stroke-width="1.4"><path d="M5 3l4 1 1 5-2 1c1 3 3 5 6 6l1-2 5 1 1 4c-1 2-3 2-5 2C9 20 4 15 3 8c0-2 0-4 2-5z"/><path d="M14 3a7 7 0 0 1 7 7M14 6a4 4 0 0 1 4 4"/></svg>
    <div>Call Us<br><b>555.014.2736</b></div>
  </div>
  <div class="abs hero-social"><span></span><span></span><span></span></div>
  <svg class="abs hero-arrow" style="left:105px" width="40" height="40" viewBox="0 0 40 40"><circle cx="20" cy="20" r="18" fill="none" stroke="#ccc" stroke-width="2"/><path d="M23 12l-8 8 8 8" fill="none" stroke="#ccc" stroke-width="2"/></svg>
  <svg class="abs hero-arrow" style="left:949px" width="40" height="40" viewBox="0 0 40 40"><circle cx="20" cy="20" r="20" fill="var(--blue)"/><path d="M17 12l8 8-8 8" fill="none" stroke="#fff" stroke-width="2.5"/></svg>
  <h1 class="abs hero-title">See What We Can<br>Do For You</h1>
  <div class="abs hero-dots"><i></i><i class="on"></i><i></i><i></i></div>
  <svg class="abs" style="left:578px;top:508px" width="42" height="18" viewBox="0 0 42 18"><path d="M2 2l19 12L40 2" fill="none" stroke="#fff" stroke-width="2"/></svg>
</section>

<section class="abs about" aria-label="About Korvel">
  <div class="abs emblem">KORVEL</div>
  <h2 class="abs">About <b>Korvel</b></h2>
  <div class="abs rule"></div>
  <div class="abs about-copy">
    <p>Lorem Ipsum is simply dummy text of the printing and typesetting industry. Lorem Ipsum has been the industry's standard</p>
    <p class="lead">Lorem Ipsum is simply dummy text of the printing and typesetting industry.</p>
    <p>Lorem Ipsum is simply dummy text of the printing and typesetting industry. Lorem Ipsum has been the industry's standard dummy text ever since the 1500s, when an unknown printer took a galley of type and scrambled it to make a type specimen book.</p>
  </div>
</section>

<h2 class="abs sec-title why-title">Why <b>Choose Us</b></h2>
<div class="abs rule why-rule"></div>

<div class="abs why-card" style="left:73px">
  <svg width="104" height="130" viewBox="0 0 104 130"><path d="M30 92A48 48 0 0 1 30 12M74 12A48 48 0 0 1 74 92" fill="none" stroke="#bbb" stroke-width="4"/><line x1="52" y1="100" x2="52" y2="118" stroke="#bbb" stroke-width="2"/><circle cx="52" cy="122" r="5" fill="#bbb"/><path d="M28 56l14-10 10 6 10-6 14 10-14 12H42z" fill="none" stroke="#444" stroke-width="2"/></svg>
  <h3>Over 10 Years Experience</h3>
  <p>Lorem Ipsum is simply dummy text of the printing and typesetting industry.</p>
</div>
<div class="abs why-card raised" style="left:422px">
  <svg width="104" height="130" viewBox="0 0 104 130"><path d="M30 92A48 48 0 0 1 30 12M74 12A48 48 0 0 1 74 92" fill="none" stroke="#bbb" stroke-width="4"/><line x1="52" y1="100" x2="52" y2="118" stroke="#bbb" stroke-width="2"/><circle cx="52" cy="122" r="5" fill="#bbb"/><rect x="40" y="42" width="24" height="26" fill="none" stroke="#444" stroke-width="2"/><circle cx="52" cy="32" r="4" fill="none" stroke="#444" stroke-width="2"/><circle cx="30" cy="55" r="4" fill="none" stroke="#444" stroke-width="2"/><circle cx="74" cy="55" r="4" fill="none" stroke="#444" stroke-width="2"/></svg>
  <h3>BEST MATERIALS</h3>
  <p>Lorem Ipsum is simply dummy text of the printing and typesetting industry.</p>
</div>
<div class="abs why-card" style="left:777px">
  <svg width="104" height="130" viewBox="0 0 104 130"><path d="M30 92A48 48 0 0 1 30 12M74 12A48 48 0 0 1 74 92" fill="none" stroke="#bbb" stroke-width="4"/><line x1="52" y1="100" x2="52" y2="118" stroke="#bbb" stroke-width="2"/><circle cx="52" cy="122" r="5" fill="#bbb"/><circle cx="52" cy="44" r="10" fill="none" stroke="#444" stroke-width="2"/><path d="M30 50v20l10 8M74 50v20l-10 8" fill="none" stroke="#444" stroke-width="2"/></svg>
  <h3>PROFESSIONAL STANDARDS</h3>
  <p>Lorem Ipsum is simply dummy text of the printing and typesetting industry.</p>
</div>

<section class="abs services" aria-label="Our services">
  <h2 class="abs sec-title">Our <b>Services</b></h2>
  <div class="abs rule"></div>
  <div class="abs emblem">KORVEL</div>

  <div class="abs svc" style="left:153px;top:190px"><h3>Electrical Services</h3><p>Lorem Ipsum is simply dummy text of the printing and typesetting industry.</p></div>
  <div class="abs svc" style="left:834px;top:154px"><h3>Data Services</h3><p>Lorem Ipsum is simply dummy text of the printing and typesetting industry.</p></div>
  <div class="abs svc" style="left:873px;top:364px"><h3>Fibre Cabling<br>Installations</h3><p>Lorem Ipsum is simply dummy text of the printing and typesetting industry.</p></div>
  <div class="abs svc" style="left:177px;top:430px"><h3>Audio Visual<br>Services</h3><p>Lorem Ipsum is simply dummy text of the printing and typesetting industry.</p></div>

  <svg class="abs svc-icon" style="left:365px;top:199px" viewBox="0 0 86 86"><path d="M8 55A36 36 0 0 1 55 8" fill="none" stroke="var(--blue)" stroke-width="4"/><circle cx="43" cy="43" r="30" fill="#fff" stroke="var(--green)" stroke-width="2"/><g fill="none" stroke="#333" stroke-width="2"><path d="M30 56V50M37 56V46M44 56V42M51 56V36M58 56V30"/><path d="M28 60h34"/></g></svg>
  <svg class="abs svc-icon" style="left:725px;top:168px" viewBox="0 0 86 86"><path d="M55 8A36 36 0 0 1 78 55" fill="none" stroke="var(--blue)" stroke-width="4"/><circle cx="43" cy="43" r="30" fill="#fff" stroke="var(--green)" stroke-width="2"/><text x="43" y="42" text-anchor="middle" font-family="Roboto,sans-serif" font-size="18" fill="#333">$</text><path d="M24 52h10l10 4 14-6" fill="none" stroke="#333" stroke-width="2"/></svg>
  <svg class="abs svc-icon" style="left:765px;top:376px" viewBox="0 0 86 86"><path d="M55 8A36 36 0 0 1 78 55" fill="none" stroke="var(--blue)" stroke-width="4"/><circle cx="43" cy="43" r="30" fill="#fff" stroke="var(--green)" stroke-width="2"/><g fill="#333"><rect x="30" y="28" width="12" height="4"/><rect x="30" y="35" width="18" height="4"/><rect x="30" y="42" width="24" height="4"/><rect x="30" y="49" width="26" height="4"/><rect x="30" y="56" width="26" height="4"/></g></svg>
  <svg class="abs svc-icon" style="left:385px;top:444px" viewBox="0 0 86 86"><path d="M8 55A36 36 0 0 1 55 8" fill="none" stroke="var(--blue)" stroke-width="4"/><circle cx="43" cy="43" r="30" fill="#fff" stroke="var(--green)" stroke-width="2"/><circle cx="45" cy="36" r="10" fill="none" stroke="#333" stroke-width="2"/><path d="M45 26v10h10M24 54h10l10 4 14-6" fill="none" stroke="#333" stroke-width="2"/></svg>

  <svg class="abs" style="left:440px;top:198px" width="322" height="322" viewBox="0 0 322 322"><g fill="#fff" stroke="var(--blue)" stroke-width="2"><circle cx="35" cy="92" r="7"/><circle cx="262" cy="46" r="7"/><circle cx="299" cy="217" r="7"/><circle cx="35" cy="236" r="7"/></g></svg>

  <a class="abs btn" href="#">Learn More &rarr;</a>

  <svg class="abs" style="left:0;top:686px" width="1200" height="40" viewBox="0 0 1200 40"><path d="M0 40Q600 -20 1200 40" fill="none" stroke="var(--green)" stroke-width="5"/><path d="M0 40Q600 -16 1200 40V40H0z" fill="#fff"/></svg>
</section>

<h2 class="abs sec-title testi-title">Our <b>Services</b></h2>
<div class="abs rule testi-rule"></div>

<article class="abs testi-card" style="left:168px">
  <div class="stars">★★★★★</div>
  <q>SOLID Service! Vety consistent!</q>
  <p>the printing and typesetting industry. Lorem Ipsum has been the industry's standard dummy text ever since the 1500s Lorem Ipsum!</p>
  <div class="author"><span class="avatar" role="img" aria-label="Client portrait"></span><div><b>Marcus Lennard</b><br>Web Development</div></div>
</article>
<article class="abs testi-card" style="left:464px">
  <div class="stars">★★★★★</div>
  <q>SOLID Service! Vety consistent!</q>
  <p>the printing and typesetting industry. Lorem Ipsum has been the industry's standard dummy text ever since the 1500s Lorem Ipsum!</p>
  <div class="author"><span class="avatar" role="img" aria-label="Client portrait"></span><div><b>Marcus Lennard</b><br>Web Development</div></div>
</article>
<article class="abs testi-card" style="left:757px">
  <div class="stars">★★★★★</div>
  <q>SOLID Service! Vety consistent!</q>
  <p>the printing and typesetting industry. Lorem Ipsum has been the industry's standard dummy text ever since the 1500s Lorem Ipsum!</p>
  <div class="author"><span class="avatar" role="img" aria-label="Client portrait"></span><div><b>Marcus Lennard</b><br>Web Development</div></div>
</article>
<div class="abs testi-dots"><i></i><i class="on"></i><i></i><i></i></div>

<section class="abs cta" aria-label="Contact us">
  <svg class="abs" style="left:0;top:0" width="400" height="197" viewBox="0 0 400 197">
    <rect width="267" height="197" fill="var(--blue)"/>
    <circle cx="267" cy="94" r="100" fill="var(--blue)"/>
    <path d="M200 60A80 80 0 0 1 320 30M345 110A80 80 0 0 1 240 170M190 120A80 80 0 0 1 188 80" fill="none" stroke="#fff" stroke-width="5"/>
    <g fill="none" stroke="#fff" stroke-width="2.5"><circle cx="267" cy="94" r="34"/><ellipse cx="267" cy="94" rx="14" ry="34"/><path d="M233 94h68M238 78h58M238 110h58M267 60v68"/></g>
  </svg>
  <p class="abs cta-text"><b>Contact us now</b> and we will<br>respond today!</p>
  <a class="abs btn" href="#">Contact Now</a>
</section>

<footer class="abs site-footer">
  <div class="brand"><span class="brand-dot"></span>KORVEL</div>
  <div class="abs foot-social"><span></span><span></span><span></span></div>
  <ul class="abs foot-links"><li>Home</li><li>About Us</li><li>Services</li><li>Gallery</li><li>Contact</li></ul>
  <form class="foot-form">
    <input style="left:671px;top:83px;width:199px;height:34px" placeholder="Name">
    <input style="left:880px;top:83px;width:199px;height:34px" placeholder="Email">
    <input style="left:671px;top:128px;width:408px;height:34px" placeholder="Subject">
    <textarea style="left:671px;top:174px;width:408px;height:92px" placeholder="Message"></textarea>
    <button class="btn" type="button">Send</button>
  </form>
  <div class="abs foot-line"></div>
  <p class="abs copyright">Copyright 2020 Korvel. All Rights Reserved.</p>
  <p class="abs legal">Privacy Policy &nbsp; | &nbsp; Terms Of Services</p>
</footer>

</body>
</html>
```